veLuna - nutrition bars - logo and packaging*

veLuna develops stress-relief nutrition bars powered by deep profiling machine learning technology, offering personalized stress management routine.
We produce 3 flavors of nutrition bars. in each flavor, we produce 6 stress relief formulations (3 for day, 3 for night) in 2 strengths.

We need a rebranding of our logo and packaging.

Target Market(s)

Full description of the target audience and their needs and lifestyle is explained in the attached presentation

Logo Text

veLuna

Font styles to use
Script

Colors

Designer to choose colors to be used in the design.

Requirements
Must have
• logo
• Packaging
• Full description of the deliveries is explained in the attached presentation
Nice to have
• concept for boxes, website

```html
<!DOCTYPE html>
<html lang="en">
<head>
<meta charset="utf-8">
<title>veLuna – Balanced Day Ritual bar wrappers</title>
<link href="https://fonts.googleapis.com/css2?family=Lato:wght@400;700&display=swap" rel="stylesheet">
<style>
  :root {
    --backdrop: #b9babc;
    --wrapper: #fbfbfb;
    --seal: #eeeeee;
    --ink-gray: #8a9197;
    --ink-soft: #8e9499;
    --green: #2e7a2a;
    --blue: #4a58a8;
    --pink: #cc3f76;
    --slate: #949ba1;
  }
  * { box-sizing: border-box; margin: 0; padding: 0; }
  html, body { width: 1200px; height: 857px; overflow: hidden; }
  body {
    background: var(--backdrop);
    font-family: "Lato", Arial, sans-serif;
    color: var(--ink-gray);
    position: relative;
  }
  .wrapper {
    position: absolute;
    top: 64px;
    width: 266px;
    height: 728px;
    background: var(--wrapper);
  }
  .wrapper::before, .wrapper::after {
    content: "";
    position: absolute;
    left: 0; right: 0;
    height: 38px;
    background: var(--seal);
  }
  .wrapper::before { top: 0; }
  .wrapper::after { bottom: 0; }
  .wrapper--green { left: 40px; }
  .wrapper--blue { left: 325px; }
  .wrapper--pink { left: 612px; }
  .wrapper--gray { left: 898px; }

  .brand {
    position: absolute;
    top: 126px;
    left: 0; right: 0;
    text-align: center;
    font-size: 52px;
    font-weight: 700;
    letter-spacing: -1px;
    color: var(--ink-gray);
    line-height: 1;
  }
  .tagline {
    position: absolute;
    top: 182px;
    right: 38px;
    font-size: 12px;
    line-height: 14px;
    color: var(--ink-soft);
    white-space: nowrap;
  }
  .emblem {
    position: absolute;
    top: 250px;
    left: 50%;
    width: 172px;
    height: 172px;
    margin-left: -86px;
    border-radius: 50%;
    border: 2px solid currentColor;
    background: radial-gradient(circle, rgba(255,255,255,0) 30%, currentColor 420%);
  }
  .wrapper--green .emblem { color: var(--green); }
  .wrapper--blue .emblem { color: var(--blue); }
  .wrapper--pink .emblem { color: var(--pink); }
  .wrapper--gray .emblem { color: var(--slate); }

  .time-icon {
    position: absolute;
    top: 470px;
    left: 50%;
    margin-left: -17px;
  }
  .variant {
    position: absolute;
    top: 506px;
    left: 50%;
    transform: translateX(-50%);
    height: 30px;
    padding: 0 14px;
    border-radius: 15px;
    color: #fff;
    font-size: 15px;
    line-height: 30px;
    white-space: nowrap;
  }
  .wrapper--green .variant { background: var(--green); font-size: 16px; }
  .wrapper--blue .variant { background: var(--blue); font-size: 14px; }
  .wrapper--pink .variant { background: var(--pink); font-size: 14px; }
  .wrapper--gray .variant { background: var(--slate); font-size: 15px; }

  .formula {
    position: absolute;
    top: 548px;
    left: 0; right: 0;
    text-align: center;
    font-size: 14px;
    line-height: 16px;
    color: var(--ink-soft);
  }
  .ingredient-icons {
    position: absolute;
    top: 568px;
    left: 50%;
    width: 74px;
    height: 30px;
    margin-left: -37px;
    border-radius: 8px;
    background: linear-gradient(90deg, #e3e5e7, #d3d6d9);
  }
  .flavour {
    position: absolute;
    top: 604px;
    left: 0; right: 0;
    text-align: center;
    font-size: 14px;
    line-height: 16px;
    letter-spacing: 0.8px;
    color: var(--ink-soft);
    white-space: nowrap;
  }
  .wrapper--pink .flavour, .wrapper--gray .flavour { letter-spacing: 0.3px; }
  .weight {
    position: absolute;
    top: 630px;
    left: 42px;
    font-size: 14px;
    line-height: 16px;
    color: var(--ink-soft);
  }
</style>
</head>
<body>

<section class="wrapper wrapper--green">
  <div class="brand">veLuna</div>
  <div class="tagline">Balanced Day Ritual</div>
  <div class="emblem" role="img" aria-label="Green geometric overlapping-circles line pattern"></div>
  <svg class="time-icon" width="34" height="26" viewBox="0 0 34 26" aria-label="Day">
    <g fill="none" stroke="#8e9499" stroke-width="2" stroke-linecap="round">
      <path d="M8 22 a9 9 0 0 1 18 0"/><line x1="2" y1="22" x2="32" y2="22"/>
      <line x1="17" y1="2" x2="17" y2="7"/><line x1="6" y1="8" x2="9" y2="11"/>
      <line x1="28" y1="8" x2="25" y2="11"/>
    </g>
  </svg>
  <div class="variant">QUIET SAGE</div>
  <div class="formula">Natural terpenes</div>
  <div class="ingredient-icons" role="img" aria-label="Small line icons of apple, date and walnut"></div>
  <div class="flavour">Dates, Apples &amp; Nuts</div>
  <div class="weight">30 gr</div>
</section>

<section class="wrapper wrapper--blue">
  <div class="brand">veLuna</div>
  <div class="tagline">Balanced Day Ritual</div>
  <div class="emblem" role="img" aria-label="Blue geometric overlapping-circles line pattern"></div>
  <svg class="time-icon" width="34" height="26" viewBox="0 0 34 26" aria-label="Night">
    <g fill="none" stroke="#8e9499" stroke-width="2" stroke-linecap="round">
      <path d="M16 3 a10 10 0 1 0 10 14 a8 8 0 0 1 -10 -14z"/>
      <path d="M25 4 v5 M22.5 6.5 h5"/><circle cx="30" cy="12" r="0.8"/>
    </g>
  </svg>
  <div class="variant">TRANQUIL INDIGO+</div>
  <div class="formula">Natural terpenes &amp; herbs</div>
  <div class="ingredient-icons" role="img" aria-label="Small line icons of apple, date and walnut"></div>
  <div class="flavour">Dates, Apples &amp; Nuts</div>
  <div class="weight">30 gr</div>
</section>

<section class="wrapper wrapper--pink">
  <div class="brand">veLuna</div>
  <div class="tagline">Balanced Day Ritual</div>
  <div class="emblem" role="img" aria-label="Pink geometric star line pattern"></div>
  <svg class="time-icon" width="34" height="26" viewBox="0 0 34 26" aria-label="Day">
    <g fill="none" stroke="#8e9499" stroke-width="2" stroke-linecap="round">
      <path d="M8 22 a9 9 0 0 1 18 0"/><line x1="2" y1="22" x2="32" y2="22"/>
      <line x1="17" y1="2" x2="17" y2="7"/><line x1="6" y1="8" x2="9" y2="11"/>
      <line x1="28" y1="8" x2="25" y2="11"/>
    </g>
  </svg>
  <div class="variant">LIVELY MAGENTA</div>
  <div class="formula">Natural terpenes &amp; herbs</div>
  <div class="ingredient-icons" role="img" aria-label="Small line icons of oats, cranberries and chocolate"></div>
  <div class="flavour">Oats, cranberries &amp; chocolate</div>
  <div class="weight">30 gr</div>
</section>

<section class="wrapper wrapper--gray">
  <div class="brand">veLuna</div>
  <div class="tagline">Balanced Day Ritual</div>
  <div class="emblem" role="img" aria-label="Gray geometric faceted line pattern"></div>
  <svg class="time-icon" width="34" height="26" viewBox="0 0 34 26" aria-label="Night">
    <g fill="none" stroke="#8e9499" stroke-width="2" stroke-linecap="round">
      <path d="M16 3 a10 10 0 1 0 10 14 a8 8 0 0 1 -10 -14z"/>
      <path d="M25 4 v5 M22.5 6.5 h5"/><circle cx="30" cy="12" r="0.8"/>
    </g>
  </svg>
  <div class="variant">DREAMY SLATE+</div>
  <div class="formula">Natural terpenes &amp; herbs</div>
  <div class="ingredient-icons" role="img" aria-label="Small line icons of oats, banana and pecan"></div>
  <div class="flavour">Oats, banana &amp; pecan</div>
  <div class="weight">30 gr</div>
</section>

</body>
</html>
```